Academic and Business book cover

I need a book cover for my academic and business book.
The focus is in international / global negotiation and influence (how to negotiate across cultures).
The book will be published on Zelvorn, both in Vaspet and printed edition. therefore I need something that works under Zelvorn guidelines.The final design should be elegant and still be able to stand out against the competition.
I would like to have orange+grey for the text colors on the cover, even if different options are welcome.
Title and my name are in the attached word doc.

Target Market(s)

graduates, Phds, from international business schools. Managers

Industry/Entity Type

Business

Font styles to use
Serif
Sans Serif

Colors

Designer to choose colors to be used in the design.

Requirements
Must have
• The title and my name should have elegant fonts.
Nice to have
• pictures of the world that don't have the "usual" Europe in the centre.

```html
<!DOCTYPE html>
<html lang="en">
<head>
<meta charset="UTF-8">
<title>The 3CS Guidebook — Book Cover</title>
<link rel="stylesheet" href="https://fonts.googleapis.com/css2?family=Anton&family=Arimo:wght@400&family=Saira+Semi+Condensed:wght@500&display=swap">
<style>
  :root {
    --sky-light: #cfe0f0;
    --sky-mid: #7fa6cf;
    --navy-deep: #0a1a3f;
    --navy-mid: #163a78;
    --map-blue: #2d6fb8;
    --title: #f5891f;
    --subtitle: #ffffff;
    --band-red: #7a1010;
    --band-line: #5a0a0a;
    --author: #f2a21c;
  }
  html, body {
    margin: 0;
    padding: 0;
    width: 800px;
    height: 1200px;
    overflow: hidden;
    background: #ffffff;
  }
  .cover {
    position: relative;
    width: 800px;
    height: 1200px;
    overflow: hidden;
    background: var(--navy-deep);
  }
  .cover-photo {
    position: absolute;
    left: 0; top: 0;
    width: 800px; height: 440px;
    background:
      linear-gradient(180deg, rgba(255,255,255,0) 55%, rgba(184,36,42,0.55) 75%, rgba(10,26,63,0.9) 100%),
      linear-gradient(180deg, var(--sky-light) 0%, var(--sky-mid) 55%, #8a9bb5 75%);
  }
  .world-map {
    position: absolute;
    left: 0; top: 400px;
    width: 800px; height: 641px;
    background:
      radial-gradient(ellipse 70% 40% at 50% 45%, rgba(45,111,184,0.75), rgba(22,58,120,0.4) 60%, rgba(10,26,63,0) 100%),
      linear-gradient(180deg, rgba(10,26,63,0) 0%, var(--navy-mid) 20%, var(--navy-deep) 100%);
  }
  .title {
    position: absolute;
    left: 0; top: 0;
    width: 800px; height: 1041px;
    margin: 0;
    font-family: "Anton", "Impact", sans-serif;
    font-weight: 400;
    text-transform: uppercase;
    color: var(--title);
  }
  .title span {
    position: absolute;
    line-height: 0.8;
    white-space: nowrap;
  }
  .title-the {
    left: 30px; top: 652px;
    font-size: 62px;
  }
  .title-number {
    left: 118px; top: 600px;
    font-size: 262px;
    letter-spacing: -2px;
  }
  .title-guide {
    left: 470px; top: 582px;
    font-size: 130px;
    letter-spacing: 2px;
  }
  .title-book {
    left: 470px; top: 714px;
    font-size: 130px;
    letter-spacing: 4px;
  }
  .subtitle {
    position: absolute;
    left: 0; top: 852px;
    width: 800px;
    margin: 0;
    text-align: center;
    font-family: "Arimo", "Arial", sans-serif;
    font-size: 33px;
    line-height: 42px;
    color: var(--subtitle);
  }
  .author-band {
    position: absolute;
    left: 0; top: 1041px;
    width: 800px; height: 159px;
    background: var(--band-red);
    border-top: 4px solid var(--band-line);
    box-sizing: border-box;
    display: flex;
    align-items: center;
    justify-content: center;
  }
  .author-name {
    margin: 0;
    font-family: "Saira Semi Condensed", "Arial Narrow", sans-serif;
    font-weight: 500;
    font-size: 56px;
    letter-spacing: 8px;
    color: var(--author);
  }
</style>
</head>
<body>
  <main class="cover">
    <div class="cover-photo" role="img" aria-label="Two businessmen shaking hands in an airport lounge with red seats and tall windows"></div>
    <div class="world-map" role="img" aria-label="Glowing world map in blue with flight arcs connecting cities across the globe"></div>

    <h1 class="title" aria-label="The 3CS Guidebook">
      <span class="title-the">The</span>
      <span class="title-number">3CS</span>
      <span class="title-guide">Guide</span>
      <span class="title-book">Book</span>
    </h1>

    <p class="subtitle">Practical Bargaining and Persuasion<br>Methods for Cross-Border Success</p>

    <footer class="author-band">
      <p class="author-name">Darvish K. Omeli</p>
    </footer>
  </main>
</body>
</html>
```